Eye Catching Business Card for Optometrist

We've recently refreshed our logo and now we need a fresh and bold look for our business cards. We provide progressive ways to improve people's vision and protect their eye health.

Use our new logo as guidance into the colors to use. As far as style goes, I love how bold and eye catching the card is for Lanternfield Studio. Feel free to use your creative judgement.

Tagline: "Clearly the best for your vision."

pertinent info to include:

Dr. Marcus Velbrin
Optometrist

7258 Dunmore Ridge Blvd #215
Brantwell, MO 64172
(555) 382-9017

marc@brantwellfamilyeyecare.example
www.brantwellfamilyeyecare.example

```html
<!DOCTYPE html>
<html lang="en">
<head>
<meta charset="utf-8">
<title>Brantwell Family Eye Care – Business Cards</title>
<link rel="stylesheet" href="https://fonts.googleapis.com/css2?family=Open+Sans:wght@400;600;700&display=swap">
<style>
  :root {
    --bg: #eceaf0;
    --card: #ffffff;
    --red: #d7262c;
    --ink: #2f2f2f;
    --muted: #555555;
    --rule: #9a9a9a;
  }
  * { box-sizing: border-box; margin: 0; padding: 0; }
  html, body { width: 1200px; height: 976px; overflow: hidden; }
  body {
    background: var(--bg);
    font-family: "Open Sans", Arial, sans-serif;
    color: var(--ink);
    position: relative;
  }
  .card {
    position: absolute;
    left: 220px;
    width: 760px;
    height: 434px;
    background: var(--card);
    border-radius: 26px;
    box-shadow: 0 4px 18px rgba(0,0,0,0.12);
    overflow: hidden;
  }
  .card--back { top: 40px; }
  .card--front { top: 502px; }

  .accent-line {
    position: absolute;
    left: 0; right: 0;
    height: 5px;
    background: var(--red);
  }
  .accent-square {
    position: absolute;
    width: 20px; height: 20px;
    background: var(--red);
    transform: translate(-50%, -50%);
  }

  .brand {
    position: absolute;
    display: flex;
    align-items: center;
    gap: 12px;
    color: var(--red);
    font-weight: 700;
    text-transform: uppercase;
    line-height: 1.1;
    white-space: nowrap;
  }
  .brand__mark {
    width: 20px; height: 20px;
    background: var(--red);
    flex: none;
  }
  .card--back .brand { left: 0; right: 0; top: 120px; justify-content: center; font-size: 30px; }
  .card--back .accent-line { top: 220px; }
  .card--back .accent-square { left: 380px; top: 222px; }
  .tagline {
    position: absolute;
    left: 0; right: 0; top: 300px;
    text-align: center;
    font-size: 22px;
    color: var(--muted);
  }

  .card--front .brand { left: 40px; top: 140px; font-size: 19px; }
  .card--front .accent-line { top: 318px; }
  .card--front .accent-square { left: 300px; top: 320px; }

  .address {
    position: absolute;
    left: 50px; top: 352px;
    font-size: 20px;
    color: var(--ink);
  }

  .contact {
    position: absolute;
    left: 410px; top: 50px;
    height: 240px;
    border-left: 2px solid var(--rule);
    padding-left: 24px;
  }
  .contact__name { font-size: 24px; font-weight: 700; letter-spacing: 0.5px; text-transform: uppercase; margin-top: 6px; }
  .contact__title { font-size: 19px; color: var(--muted); margin-bottom: 30px; }
  .contact__list { list-style: none; }
  .contact__item {
    position: relative;
    font-size: 16px;
    line-height: 36px;
  }
  .contact__item::before {
    content: "";
    position: absolute;
    left: -36px; top: 11px;
    width: 22px; height: 14px;
    background: var(--red);
  }
</style>
</head>
<body>
  <section class="card card--back" aria-label="Card back">
    <div class="brand"><span class="brand__mark"></span>Brantwell Family Eye Care</div>
    <div class="accent-line"></div>
    <div class="accent-square"></div>
    <p class="tagline">Clearly the best for your vision.</p>
  </section>

  <section class="card card--front" aria-label="Card front">
    <div class="brand"><span class="brand__mark"></span>Brantwell Family Eye Care</div>
    <div class="contact">
      <p class="contact__name">Dr. Marcus Velbrin</p>
      <p class="contact__title">Optometrist</p>
      <ul class="contact__list">
        <li class="contact__item">(555) 382-9017</li>
        <li class="contact__item">marc@brantwellfamilyeyecare.example</li>
        <li class="contact__item">www.brantwellfamilyeyecare.example</li>
      </ul>
    </div>
    <div class="accent-line"></div>
    <div class="accent-square"></div>
    <p class="address">7258 Dunmore Ridge Blvd #215, Brantwell, MO 64172</p>
  </section>
</body>
</html>
```